zorvan lumet website design

An IT support and IT Security Company - just use dummy text for now for the design. Examples of sites we like the looks and feel of but need it more professional feel are like: www.kelbrovault.uk.com , www.pravok.co.uk, www.quenthardy.com/professional/, www.vur.com, www.melvish.com,

Best to message me if you have any questions

Target Market(s)

small to medium UK based companies that require IT support services

Industry/Entity Type

It Company

Contact Information for Business Card

use dummy name, telephone and email for now, will provide details later.

Logo Text

zorvan lumet (and then below the logo it should say "your IT, networks and security partner")

Coding

Coded - Design and coding required

Number of Pages Required

5+ page

Colors

Designer to choose colors to be used in the design.

Requirements
Must have
• must be professional, yet simple and clear that this is a serious IT support and IT security company.
Nice to have
• 1)The website homepage must have professional quality pictures of IT support or London city skyline or any picture that projects friendly business partners, professionalism and ready to serve.
• 2) Home page needs to include tabs for following pages 'Services' , 'About Us' , 'Contact Us' 'Home'
• 3) Website built customised using wordpress is ideal and easy for us to manage.
• more room for boxed options from homepage (with pic or image in background)
Should not have
• no checkout trolleys or payment options.

```html
<!DOCTYPE html>
<html lang="en">
<head>
<meta charset="utf-8">
<title>Zorvan Lumet – IT Support &amp; Security</title>
<link rel="stylesheet" href="https://fonts.googleapis.com/css2?family=Oswald:wght@400;500&family=Roboto:wght@400;500;700&display=swap">
<style>
:root{
  --purple:#7a4fa3;
  --red:#f2425a;
  --amber:#f8b236;
  --ink:#2b2b2b;
  --body:#6a6a6a;
  --nav:#7b7b7b;
  --tint:#f3f3f3;
  --line:#d6d6d6;
  --footer:#a7a7a7;
  --white:#ffffff;
}
*{box-sizing:border-box;margin:0;padding:0}
html,body{width:706px;height:1200px;overflow:hidden}
body{position:relative;background:var(--white);font-family:"Roboto",Arial,sans-serif;color:var(--body)}
.abs{position:absolute}
.band-top{left:0;top:0;width:706px;height:462px;background:var(--tint)}
.band-top .white-head{position:absolute;left:0;top:0;width:706px;height:66px;background:var(--white)}
.band-news{left:0;top:800px;width:706px;height:400px;background:var(--tint)}

/* header */
.brand{left:124px;top:6px;display:flex;align-items:center;gap:6px}
.brand-mark{width:22px;height:26px;background:var(--purple);border-radius:3px}
.brand-text{display:flex;flex-direction:column}
.brand-name{font-family:"Oswald",sans-serif;font-weight:500;font-size:18px;line-height:20px;color:var(--purple);letter-spacing:.2px}
.brand-tag{font-size:5.6px;line-height:7px;color:var(--body);letter-spacing:.1px}
.contact{display:flex;gap:7px;align-items:flex-start;top:10px;font-size:6.4px;color:var(--ink);line-height:9px}
.contact b{font-weight:700;display:block}
.contact .ico{width:18px;height:18px;background:var(--red);display:flex;align-items:center;justify-content:center}
.social{left:520px;top:14px;display:flex;gap:4px}
.social span{width:14px;height:14px;border-radius:50%;background:var(--purple)}

/* nav */
.nav{left:118px;top:42px;width:471px;height:20px;background:var(--nav);display:flex;font-size:7.2px;font-weight:500;color:var(--white)}
.nav a{color:inherit;text-decoration:none;display:flex;align-items:center;gap:6px;padding-left:12px;border-right:1px solid #bcbcbc}
.nav a.active{background:var(--red);border-right:none}
.nav .login{margin-left:auto;border:none;padding-right:10px}

/* hero */
.hero{left:118px;top:68px;width:471px;height:263px;background:linear-gradient(180deg,#4a4a4a 0%,#2d2d2d 45%,#6c6c6c 100%)}
.hero-copy{right:43px;top:72px;text-align:right;color:var(--white)}
.hero-title{font-family:"Oswald",sans-serif;font-weight:400;font-size:30px;line-height:1.1;margin-bottom:8px}
.hero-copy p{font-size:8.4px;line-height:13.5px}
.hero-btn{right:43px;top:167px;width:72px;height:24px;background:var(--purple);color:var(--white);font-size:7px;font-weight:700;display:flex;align-items:center;justify-content:center}
.arrow{top:121px;width:22px;height:22px;background:var(--white);display:flex;align-items:center;justify-content:center}

/* intro */
.intro{left:118px;top:346px;width:471px;height:88px;background:var(--white);border:1px solid var(--line)}
.intro h2{position:absolute;left:10px;top:22px;font-family:"Oswald",sans-serif;font-weight:400;font-size:18.5px;line-height:21px;color:var(--ink)}
.intro .rule{position:absolute;left:144px;top:18px;width:2px;height:52px;background:var(--purple)}
.intro p{position:absolute;left:159px;top:20px;width:296px;font-size:6.9px;line-height:11.6px}

.sec-title{font-family:"Oswald",sans-serif;font-weight:400;font-size:18px;color:var(--ink);display:flex;align-items:center;gap:8px}
.sec-title::after{content:"";width:2px;height:18px;background:var(--purple)}

/* services */
.card{top:509px;width:141px;height:113px;color:var(--white);padding:10px 8px}
.card .head{display:flex;align-items:center;gap:8px;height:36px;font-size:8.6px;font-weight:500;line-height:10.5px}
.card .head svg{flex:none}
.card p{font-size:6.8px;line-height:12px;margin-top:5px}
.card .more{font-size:6.6px;font-weight:700;margin-top:4px;display:flex;gap:4px;align-items:center}
.card.purple{left:118px;background:var(--purple)}
.card.red{left:282px;background:var(--red)}
.card.amber{left:447px;background:var(--amber)}

/* about */
.about{left:118px;top:642px;width:471px;height:140px;border:1px solid var(--line);text-align:center}
.about h2{margin-top:14px;display:flex;align-items:center;justify-content:center;gap:8px;font-family:"Oswald",sans-serif;font-weight:400;font-size:18px;color:var(--ink)}
.about h2::before,.about h2::after{content:"";width:53px;height:1.5px;background:var(--purple)}
.about p{width:413px;margin:9px auto 0;font-size:6.8px;line-height:11.6px}
.btn{background:var(--purple);color:var(--white);font-size:7px;font-weight:700;display:flex;align-items:center;justify-content:center}
.about .btn{width:71px;height:24px;margin:16px auto 0}

/* news */
.news{top:854px;width:236px}
.news .top{display:flex;gap:9px}
.date{flex:none;width:26px;height:32px;background:var(--red);color:var(--white);font-size:7.4px;font-weight:700;text-align:center;padding-top:3px;line-height:12px}
.date i{display:block;width:18px;height:1px;background:var(--white);margin:1px auto 2px}
.news h3{width:180px;font-weight:400;font-size:9.6px;line-height:12.6px;color:var(--ink);padding-top:2px}
.news p{width:214px;margin-top:15px;font-size:6.6px;line-height:11.8px}
.news .btn{width:58px;height:21px;margin-top:17px;font-size:6.6px}

/* footer */
.footer{left:118px;top:1022px;width:471px;height:145px;background:var(--footer);color:#444}
.newsletter{position:absolute;left:14px;top:18px;display:flex;align-items:center;gap:10px}
.newsletter h2{font-family:"Oswald",sans-serif;font-weight:500;font-size:14.5px;color:#333;display:flex;gap:7px;align-items:center;margin-right:6px}
.newsletter h2::after{content:"";width:1.5px;height:17px;background:#333}
.field{width:127px;height:24px;background:var(--white);font-size:6.4px;color:#999;padding:8px 9px}
.send{width:58px;height:24px;gap:8px}
.footer .divider{position:absolute;left:0;top:54px;width:471px;height:1px;background:#bdbdbd}
.col{position:absolute;top:66px;font-size:6.8px;line-height:12.8px}
.col h4{font-weight:400;font-size:7.6px;letter-spacing:.2px;color:#3a3a3a;margin-bottom:4px}
.col .row{display:flex;gap:8px;align-items:flex-start;margin-bottom:3px;line-height:8.6px}
.fsocial{display:flex;gap:4px;margin:3px 0 4px}
.fsocial span{width:15px;height:15px;border:1px solid #555;border-radius:50%}
.copy{left:118px;top:1178px;font-size:6.4px;color:#444}
</style>
</head>
<body>
<div class="abs band-top"><div class="white-head"></div></div>
<div class="abs band-news"></div>

<header>
  <div class="abs brand"><span class="brand-mark"></span>
    <span class="brand-text"><span class="brand-name">ZORVAN LUMET</span><span class="brand-tag">your IT, networks and security partner</span></span>
  </div>
  <div class="abs contact" style="left:308px">
    <span class="ico"><svg width="9" height="9" viewBox="0 0 10 10"><path d="M2 1l2 2-1 1.3c.6 1.2 1.5 2.1 2.7 2.7L7 6l2 2-1.3 1.3C4.5 9 1 5.5.7 2.3z" fill="#fff"/></svg></span>
    <div><b>CALL :</b>+4420796543</div>
  </div>
  <div class="abs contact" style="left:398px">
    <span class="ico"><svg width="10" height="8" viewBox="0 0 10 8"><rect x=".5" y=".5" width="9" height="7" fill="none" stroke="#fff"/><path d="M.5.5L5 4.5 9.5.5" fill="none" stroke="#fff"/></svg></span>
    <div><b>E-MAIL :</b>info@zorvanlumet.uk.com</div>
  </div>
  <div class="abs social"><span></span><span></span><span></span><span></span></div>
</header>

<nav class="abs nav">
  <a class="active" href="#" style="width:67px"><svg width="10" height="9" viewBox="0 0 10 9"><path d="M5 0L0 4.5h1.5V9h2.5V6h2v3h2.5V4.5H10z" fill="#fff"/></svg>Home</a>
  <a href="#" style="width:76px"><svg width="10" height="10" viewBox="0 0 10 10"><circle cx="5" cy="5" r="3" fill="none" stroke="#fff" stroke-width="1.5"/></svg>Service</a>
  <a href="#" style="width:83px"><svg width="9" height="9" viewBox="0 0 9 9"><circle cx="4.5" cy="2.5" r="2.3" fill="#fff"/><path d="M0 9c0-3 2-4 4.5-4S9 6 9 9z" fill="#fff"/></svg>About Us</a>
  <a href="#" style="width:auto;border:none"><svg width="6" height="10" viewBox="0 0 6 10"><rect x=".5" y=".5" width="5" height="9" rx="1" fill="none" stroke="#fff"/></svg>Contact Us</a>
  <a class="login" href="#"><svg width="8" height="10" viewBox="0 0 8 10"><rect x="0" y="4" width="8" height="6" fill="#fff"/><path d="M2 4V2.5a2 2 0 014 0V4" fill="none" stroke="#fff" stroke-width="1.2"/></svg>Login</a>
</nav>

<section class="abs hero" role="img" aria-label="Photo of a server room with rows of dark server racks">
  <div class="abs hero-copy">
    <h1 class="hero-title">Welcome To The Zorvan Lumet</h1>
    <p>Lorem Ipsum is simply dummy text of the printing and typesetting industry.<br>Lorem Ipsum has been the industry's standard</p>
  </div>
  <div class="abs hero-btn">READ MORE</div>
  <div class="abs arrow" style="left:0"><svg width="9" height="6" viewBox="0 0 9 6"><path d="M9 3H1M3 .5L.5 3 3 5.5" fill="none" stroke="#222"/></svg></div>
  <div class="abs arrow" style="right:0"><svg width="9" height="6" viewBox="0 0 9 6"><path d="M0 3h8M6 .5L8.5 3 6 5.5" fill="none" stroke="#222"/></svg></div>
</section>

<section class="abs intro">
  <h2>IT Support for Your<br>Industry</h2>
  <span class="rule"></span>
  <p>Lorem Ipsum is simply dummy text of the printing and typesetting industry. Lorem Ipsum has been the industry's standard dummy text ever since the 1500s, when an unknown printer took a galley of type and scrambled it to make a type specimen book. It has survived not only five centuries, but also the leap into electronic..</p>
</section>

<h2 class="abs sec-title" style="left:118px;top:476px">Our Services</h2>

<article class="abs card purple">
  <div class="head"><svg width="34" height="30" viewBox="0 0 34 30"><path d="M6 15a11 11 0 0 1 19-7.5M28 15a11 11 0 0 1-19 7.5" fill="none" stroke="#fff" stroke-width="2"/><rect x="12" y="9" width="10" height="12" fill="#fff"/></svg>Business Continuity</div>
  <p>Lorem Ipsum is simply dummy text of the printing and typesetting industry. Lorem Ipsum dummy text....</p>
  <div class="more">READ MORE <svg width="8" height="5" viewBox="0 0 8 5"><path d="M0 2.5h7M5 .5l2 2-2 2" fill="none" stroke="#fff"/></svg></div>
</article>
<article class="abs card red">
  <div class="head"><svg width="32" height="32" viewBox="0 0 32 32"><circle cx="16" cy="11" r="7" fill="none" stroke="#fff" stroke-width="3" stroke-dasharray="3 2"/><circle cx="16" cy="11" r="3" fill="#fff"/><path d="M3 18c2 6 6 10 13 12 7-2 11-6 13-12" fill="none" stroke="#fff" stroke-width="2.5"/></svg>IT Support &amp; Field<br>Services</div>
  <p>Lorem Ipsum is simply dummy text of the printing and typesetting industry. Lorem Ipsum dummy text....</p>
  <div class="more">READ MORE <svg width="8" height="5" viewBox="0 0 8 5"><path d="M0 2.5h7M5 .5l2 2-2 2" fill="none" stroke="#fff"/></svg></div>
</article>
<article class="abs card amber">
  <div class="head"><svg width="30" height="34" viewBox="0 0 30 34"><circle cx="15" cy="12" r="7" fill="#fff"/><path d="M6 12a9 9 0 0118 0" fill="none" stroke="#fff" stroke-width="2"/><path d="M1 34c0-8 6-12 14-12s14 4 14 12z" fill="#fff"/></svg>Outsourced Service<br>Desk</div>
  <p>Lorem Ipsum is simply dummy text of the printing and typesetting industry. Lorem Ipsum dummy text....</p>
  <div class="more">READ MORE <svg width="8" height="5" viewBox="0 0 8 5"><path d="M0 2.5h7M5 .5l2 2-2 2" fill="none" stroke="#fff"/></svg></div>
</article>

<section class="abs about">
  <h2>About Us</h2>
  <p>Lorem Ipsum is simply dummy text of the printing and typesetting industry. Lorem Ipsum has been the industry's standard dummy text ever since the 1500s, when an unknown printer took a galley of type and scrambled it to make a type specimen book. It has survived not only five centuries, but also the leap into electronic..</p>
  <div class="btn">READ MORE</div>
</section>

<h2 class="abs sec-title" style="left:118px;top:820px">Our News</h2>

<article class="abs news" style="left:118px">
  <div class="top"><div class="date">15<i></i>Feb</div><h3>Lorem Ipsum is simply dummy text of the printing and typesetting industry.</h3></div>
  <p>Lorem Ipsum is simply dummy text of the printing and typesettingdus-try. Lorem Ipsum has been the industry's standard dummy text ever since the 1500s, when an unknown printer took a galley of type and scrambled it to make a type specimen book.</p>
  <div class="btn">READ MORE</div>
</article>
<article class="abs news" style="left:365px">
  <div class="top"><div class="date">15<i></i>Feb</div><h3>Lorem Ipsum is simply dummy text of the printing and typesetting industry.</h3></div>
  <p>Lorem Ipsum is simply dummy text of the printing and typesettingdus-try. Lorem Ipsum has been the industry's standard dummy text ever since the 1500s, when an unknown printer took a galley of type and scrambled it to make a type specimen book.</p>
  <div class="btn">READ MORE</div>
</article>

<footer class="abs footer">
  <div class="newsletter">
    <h2>OUR NEWSLETER</h2>
    <div class="field">Name</div>
    <div class="field">E-mail Address</div>
    <div class="btn send">SEND <svg width="12" height="10" viewBox="0 0 12 10"><path d="M0 4.5L12 0 9 10 6 6.5z" fill="#fff"/></svg></div>
  </div>
  <div class="divider"></div>
  <div class="col" style="left:13px"><h4>COMPNAY</h4>Home<br>Services<br>About Us<br>Contact Us</div>
  <div class="col" style="left:101px"><h4>QUICK LINKS</h4>News<br>Account<br>Login<br>Help</div>
  <div class="col" style="left:205px"><h4>KEEP IN TOUCH</h4>
    <div class="row"><svg width="8" height="8" viewBox="0 0 10 10"><path d="M2 1l2 2-1 1.3c.6 1.2 1.5 2.1 2.7 2.7L7 6l2 2-1.3 1.3C4.5 9 1 5.5.7 2.3z" fill="#444"/></svg><span style="padding-left:6px">+4420796543</span></div>
    <div class="row"><svg width="8" height="9" viewBox="0 0 8 10"><path d="M4 0a4 4 0 00-4 4c0 3 4 6 4 6s4-3 4-6a4 4 0 00-4-4z" fill="#444"/></svg><span style="padding-left:6px">Lorem Ipsum is simply dummy text<br>of the printing</span></div>
    <div class="row"><svg width="9" height="7" viewBox="0 0 10 8"><rect x=".5" y=".5" width="9" height="7" fill="none" stroke="#444"/><path d="M.5.5L5 4.5 9.5.5" fill="none" stroke="#444"/></svg><span style="padding-left:5px">info@zorvanlumet.uk.com</span></div>
  </div>
  <div class="col" style="left:376px"><h4>FOLLOW US</h4>
    <div class="fsocial"><span></span><span></span><span></span><span></span></div>
    <div style="line-height:10px">Privacy Policy<br>Terms and Condition</div>
  </div>
</footer>
<p class="abs copy">© Copyright 2018 zorvan lumet.&nbsp; All Rights Reserved.</p>
</body>
</html>
```